New Innovative Counselling and psychotherapy Service needs Business Card design

Keep it simple and professional. On one side, just company name and logo (perhaps in all blue) and maybe a tag line.

On other side (all white) my name and Qualifications in centre

Industry/Entity Type

Health And Wellness

Contact Information for Business Card

Dara Whelby
Counsellor & Psychotherapist
BSc (Psychol.), BA, Dip. (Couns. & Psych.), PG.Cert (CBT), FGTrK, ONRE

I will also require Mobile no, Email and web site address of which I'll pass on to final designer.

Font styles to use
Sans Serif

Requirements
Must have
• My Logo Only and please use the colours in logo that is in it.
Should not have
• Any other images

```html
<!DOCTYPE html>
<html lang="en">
<head>
<meta charset="utf-8">
<title>Harbor Grove – Business Card</title>
<link href="https://fonts.googleapis.com/css2?family=Open+Sans:wght@400;600;700&display=swap" rel="stylesheet">
<style>
  :root {
    --stage: #2b2c2e;
    --green-light: #d8efa0;
    --green: #8fd15a;
    --blue: #3fb0ec;
    --blue-deep: #2f9fe0;
    --white: #f7f7f7;
    --ink: #4a4d50;
    --tag-ink: #5e6a55;
  }
  * { margin: 0; padding: 0; box-sizing: border-box; }
  html, body {
    width: 1200px; height: 900px; overflow: hidden;
    background: var(--stage);
    font-family: "Open Sans", Arial, sans-serif;
  }
  .stage { position: relative; width: 1200px; height: 900px; }
  .card {
    position: absolute; width: 620px; height: 354px;
    box-shadow: 0 10px 30px rgba(0,0,0,.45);
    overflow: hidden;
  }
  /* front */
  .card-front {
    left: 150px; top: 80px;
    background: linear-gradient(90deg, var(--green-light) 0%, var(--green) 55%, var(--green) 100%);
  }
  .front-brand {
    position: absolute; left: 0; right: 0; top: 110px;
    display: flex; align-items: center; justify-content: center; gap: 14px;
  }
  .brand-dot { width: 44px; height: 44px; border-radius: 50%; background: var(--blue); }
  .front-brand .brand-name { font-size: 34px; font-weight: 600; color: var(--blue-deep); }
  .tagline {
    position: absolute; left: 0; right: 0; bottom: 34px; text-align: center;
    font-size: 15px; color: var(--tag-ink); letter-spacing: .2px;
  }
  /* back */
  .card-back { left: 430px; top: 470px; background: var(--white); display: flex; }
  .panel-info {
    width: 46%; height: 100%;
    background: linear-gradient(160deg, var(--blue-deep), var(--blue));
    color: #fff; padding: 44px 0 0 34px; position: relative;
  }
  .holder-name { font-size: 21px; font-weight: 700; text-transform: uppercase; letter-spacing: .3px; }
  .holder-role { margin-top: 10px; font-size: 15px; text-transform: uppercase; letter-spacing: .3px; }
  .holder-quals { margin-top: 3px; font-size: 11.5px; line-height: 1.45; }
  .contacts { position: absolute; left: 34px; bottom: 34px; list-style: none; }
  .contacts li { display: flex; align-items: center; gap: 10px; font-size: 13.5px; line-height: 21px; }
  .contacts svg { width: 14px; height: 14px; flex: none; }
  .panel-brand {
    flex: 1; display: flex; align-items: center; justify-content: center; gap: 12px;
  }
  .panel-brand .brand-dot { width: 34px; height: 34px; }
  .panel-brand .brand-name { font-size: 27px; font-weight: 400; color: var(--ink); }
</style>
</head>
<body>
<main class="stage">
  <section class="card card-front">
    <div class="front-brand">
      <span class="brand-dot"></span>
      <span class="brand-name">Harbor Grove</span>
    </div>
    <p class="tagline">Caring For Your Psychological Well-Being Is Our Top Priority</p>
  </section>

  <section class="card card-back">
    <div class="panel-info">
      <h1 class="holder-name">Dara Whelby</h1>
      <p class="holder-role">Counsellor &amp; Psychotherapist</p>
      <p class="holder-quals">BSc (Psychol.), BA, Dip. (Couns. &amp; Psych.)<br>PG.Cert (CBT), FGTrK,</p>
      <ul class="contacts">
        <li>
          <svg viewBox="0 0 14 14" aria-hidden="true"><rect x="3.5" y="0.8" width="7" height="12.4" rx="1.3" fill="none" stroke="#fff" stroke-width="1.3"/><circle cx="7" cy="11" r=".8" fill="#fff"/></svg>
          555 201 4478
        </li>
        <li>
          <svg viewBox="0 0 14 14" aria-hidden="true"><rect x="1" y="3" width="12" height="8.5" fill="#fff"/><path d="M1 3 L7 8 L13 3" fill="none" stroke="var(--blue)" stroke-width="1.2"/></svg>
          dara@harborgrove.com
        </li>
        <li>
          <svg viewBox="0 0 14 14" aria-hidden="true"><circle cx="7" cy="7" r="6" fill="#fff"/><ellipse cx="7" cy="7" rx="2.4" ry="6" fill="none" stroke="var(--blue)" stroke-width="1"/><path d="M1 7 H13" stroke="var(--blue)" stroke-width="1"/></svg>
          www.harborgrove.com
        </li>
      </ul>
    </div>
    <div class="panel-brand">
      <span class="brand-dot"></span>
      <span class="brand-name">Harbor Grove</span>
    </div>
  </section>
</main>
</body>
</html>
```